Informational Site for Advanced Chemistry R&D

The company develops oxidation chemistry for air, water, fuel pollution controls. The site has been prototyped at www.velquaresearch.example. Take a look. Now, the task is to design it for eye-catching beauty with use of color, on-page scroll-driven color transition and parallax effects. Should capture the themes: high technology, wow it's beautiful, modern, uncluttered, clean urban environment.

Target Market(s)

China Environmentally Conscious Government and Industry,

Industry/Entity Type

It Company

Number of Pages Required

3 page

Font styles to use
Sans Serif

Requirements
Must have
• Parallax effects, desktop compatible, Rich, Modern, Simple, Graphic
Nice to have
• Mobile Phone Compatible
Should not have
• Flash, or anything that is slow to load or requires high bandwidth

```html
<!DOCTYPE html>
<html lang="en">
<head>
<meta charset="utf-8">
<title>Velqua — Advanced Oxidation Science</title>
<link rel="stylesheet" href="https://fonts.googleapis.com/css2?family=Open+Sans:wght@400;600;700&family=Raleway:wght@400;600;700&display=swap">
<style>
:root{
  --blue:#1b8fd4;
  --blue-deep:#0f6eb2;
  --blue-dark:#0b5a94;
  --sky:#7cc6f0;
  --grass:#5fae3a;
  --ink:#333;
  --grey:#888;
  --light:#f4f6f8;
  --footer:#262a2e;
  --footer-bottom:#16191c;
  --white:#fff;
}
*{box-sizing:border-box;margin:0;padding:0}
html,body{width:1200px;height:2448px;overflow:hidden;background:var(--white)}
body{font-family:"Open Sans",Arial,sans-serif;color:var(--ink);position:relative}
h1,h2,h3{font-family:"Raleway","Open Sans",sans-serif}

/* header */
.site-header{position:absolute;top:0;left:0;width:1200px;height:144px;background:var(--white)}
.account-links{position:absolute;top:10px;right:56px;font-size:11px;color:var(--grey);letter-spacing:.5px}
.brand{position:absolute;left:56px;top:44px;display:flex;align-items:center;gap:12px}
.brand-dot{width:46px;height:46px;border-radius:50%;background:var(--blue)}
.brand-name{font-family:"Open Sans",sans-serif;font-weight:700;font-size:34px;color:var(--blue)}
.main-nav{position:absolute;right:40px;top:48px;display:flex}
.nav-item{width:110px;text-align:center;font-size:14px;color:#555}
.nav-item svg{display:block;margin:0 auto 6px}
.nav-item.active{color:var(--blue);font-weight:600}
.nav-item.active::after{content:"";display:block;width:40px;height:3px;background:var(--blue);margin:10px auto 0}

/* hero */
.hero{position:absolute;top:144px;left:0;width:1200px;height:496px}
.hero-photo{position:absolute;inset:0;
  background:linear-gradient(180deg,#2d8fd8 0%,var(--sky) 55%,#bfe3a0 72%,var(--grass) 100%)}
.hero-copy{position:absolute;left:100px;top:100px;width:580px;padding:22px 28px;background:rgba(10,60,110,.3);color:var(--white)}
.hero-copy h1{font-weight:600;font-size:25px;line-height:1.35}
.hero-copy p{font-size:13px;margin:12px 0;opacity:.9;line-height:1.5}
.hero-list{list-style:none;font-size:13px}
.hero-list li{display:flex;align-items:center;gap:8px;margin-top:5px}

/* advanced oxidation */
.advanced{position:absolute;top:640px;left:0;width:1200px;height:320px}
.advanced-text{position:absolute;left:100px;top:72px;width:600px}
.section-title{font-size:24px;font-weight:400;color:#666;letter-spacing:1px}
.advanced-text p{font-size:13px;line-height:1.7;color:var(--grey);margin-top:14px}
.btn{display:inline-block;margin-top:22px;background:var(--blue-deep);color:var(--white);font-size:13px;padding:10px 26px;border-radius:3px}
.molecule{position:absolute;left:830px;top:40px;width:290px;height:240px;border-radius:8px;
  background:linear-gradient(160deg,#f3f8fc 0%,#e4f1fa 60%,#fbf3d6 100%)}

/* features band */
.features{position:absolute;top:960px;left:0;width:1200px;height:240px;background:var(--blue)}
.features .wave{position:absolute;top:0;left:0}
.feature{position:absolute;width:190px;text-align:center;color:var(--white)}
.feature-icon{width:76px;height:76px;border-radius:50%;background:var(--blue-deep);border:4px solid var(--white);
  margin:0 auto 8px;display:flex;align-items:center;justify-content:center}
.feature h3{font-size:15px;font-weight:600}
.feature p{font-size:11px;opacity:.85;line-height:1.4;margin-top:3px}

/* solutions */
.solutions{position:absolute;top:1200px;left:0;width:1200px;height:680px;
  background:linear-gradient(180deg,var(--blue) 0%,var(--blue-deep) 100%);color:var(--white);text-align:center}
.solutions .section-title{color:var(--white);padding-top:44px}
.solutions-intro{width:820px;margin:14px auto 0;font-size:13px;line-height:1.6;opacity:.9}
.solution-grid{position:absolute;left:100px;top:176px;width:1000px;height:410px;background:var(--white);
  padding:18px;display:flex;gap:18px;text-align:left}
.solution-card{flex:1;color:var(--ink)}
.solution-photo{height:200px}
.solution-card h3{font-family:"Open Sans",sans-serif;font-size:13px;color:var(--blue-deep);font-weight:600;margin-top:12px;white-space:nowrap}
.solution-card p{font-size:11.5px;line-height:1.55;color:var(--grey);margin-top:6px}
.solution-card .more{font-size:12px;color:var(--blue-deep);margin-top:8px;display:block}
.solutions .wave-bottom{position:absolute;left:0;bottom:0}

/* partners */
.partners{position:absolute;top:1880px;left:0;width:1200px;height:370px;text-align:center}
.partners-head{display:flex;align-items:center;justify-content:center;gap:20px;margin-top:24px}
.partners-head span{width:140px;height:1px;background:#ccc}
.partners-head h2{font-size:24px;font-weight:400;color:var(--blue-deep);letter-spacing:1px}
.partner-row{display:flex;justify-content:center;gap:110px;margin-top:40px}
.partner{width:170px}
.partner-badge{width:150px;height:150px;border-radius:50%;margin:0 auto;background:var(--light);border:2px solid #dde3ea;
  display:flex;align-items:center;justify-content:center}
.partner-badge .brand-name{font-size:26px}
.partner-shape{width:90px;height:90px;border-radius:50%}
.partner p{font-size:12px;color:var(--grey);margin-top:14px;line-height:1.5}

/* footer */
.site-footer{position:absolute;top:2250px;left:0;width:1200px;height:150px;background:var(--footer);color:#ccc}
.footer-col{position:absolute;top:22px}
.footer-col h4{font-family:"Raleway",sans-serif;color:var(--white);font-size:15px;letter-spacing:1px;margin-bottom:10px}
.footer-col p{font-size:11px;line-height:1.6}
.footer-col .btn{margin-top:10px;padding:6px 16px;font-size:11px}
.contact-line{display:flex;align-items:center;gap:8px;font-size:11px;margin-bottom:6px}
.social{display:grid;grid-template-columns:repeat(4,26px);gap:6px}
.social span{width:26px;height:26px;border-radius:3px}
.footer-brand{position:absolute;right:70px;top:44px;display:flex;align-items:center;gap:12px}
.footer-brand .brand-dot{background:var(--white)}
.footer-brand .brand-name{color:var(--white);font-size:30px}
.footer-bottom{position:absolute;top:2400px;left:0;width:1200px;height:48px;background:var(--footer-bottom);
  color:#999;font-size:11px;display:flex;align-items:center;justify-content:space-between;padding:0 56px}
</style>
</head>
<body>

<header class="site-header">
  <div class="account-links">LOG IN &nbsp;|&nbsp; REGISTER</div>
  <div class="brand"><span class="brand-dot"></span><span class="brand-name">Velqua</span></div>
  <nav class="main-nav">
    <div class="nav-item active">
      <svg width="22" height="20" viewBox="0 0 22 20"><path d="M2 10 L11 2 L20 10 M5 8 V18 H17 V8" fill="none" stroke="#1b8fd4" stroke-width="2"/></svg>Home</div>
    <div class="nav-item">
      <svg width="22" height="20" viewBox="0 0 22 20"><circle cx="8" cy="8" r="5" fill="none" stroke="#1b8fd4" stroke-width="2"/><circle cx="16" cy="14" r="4" fill="none" stroke="#1b8fd4" stroke-width="2"/></svg>Technology</div>
    <div class="nav-item">
      <svg width="22" height="20" viewBox="0 0 22 20"><path d="M2 12 L20 4 L14 18 L11 12 Z" fill="#1b8fd4"/></svg>Products</div>
    <div class="nav-item">
      <svg width="22" height="20" viewBox="0 0 22 20"><circle cx="11" cy="10" r="7" fill="none" stroke="#1b8fd4" stroke-width="2"/><circle cx="11" cy="10" r="2.5" fill="#1b8fd4"/></svg>Solutions</div>
    <div class="nav-item">
      <svg width="22" height="20" viewBox="0 0 22 20"><path d="M5 2 L9 2 L10 7 L7 9 Q9 13 13 15 L15 12 L20 13 L20 17 Q10 19 4 8 Z" fill="#1b8fd4"/></svg>Contacts</div>
  </nav>
</header>

<section class="hero">
  <div class="hero-photo" role="img" aria-label="Photo of an open hand holding a green globe above a grass field under blue sky"></div>
  <div class="hero-copy">
    <h1>Advanced OxidationScience<br>for Environmental Pollution Management</h1>
    <p>Desulfurization and denitrification using our proprietary flue gas treatment process, clean and efficient.</p>
    <ul class="hero-list">
      <li><svg width="12" height="12" viewBox="0 0 12 12"><path d="M1 6 L5 10 L11 2" fill="none" stroke="#fff" stroke-width="2"/></svg>Water</li>
      <li><svg width="12" height="12" viewBox="0 0 12 12"><path d="M1 6 L5 10 L11 2" fill="none" stroke="#fff" stroke-width="2"/></svg>Air</li>
      <li><svg width="12" height="12" viewBox="0 0 12 12"><path d="M1 6 L5 10 L11 2" fill="none" stroke="#fff" stroke-width="2"/></svg>Fuel</li>
    </ul>
  </div>
</section>

<section class="advanced">
  <div class="advanced-text">
    <h2 class="section-title">ADVANCED OXIDATION</h2>
    <p>Desulfurization and denitrification using our proprietary flue gas treatment process. Sulfur and nitrogen are oxidized and absorbed into an environmentally friendly solid residue, for safe removal from fuel and wastewater. Simple, reliable design using our proprietary reactive agents.</p>
    <a class="btn">Read More &gt;&gt;</a>
  </div>
  <div class="molecule" role="img" aria-label="Illustration of reactive molecules linked around a central oxidant"></div>
</section>

<section class="features">
  <svg class="wave" width="1200" height="120" viewBox="0 0 1200 120" preserveAspectRatio="none">
    <path d="M0 0 H1200 V40 Q1050 100 900 60 Q750 20 600 70 Q450 120 300 70 Q150 20 0 60 Z" fill="#fff"/>
  </svg>
  <div class="feature" style="left:50px;top:64px">
    <div class="feature-icon"><svg width="34" height="34" viewBox="0 0 34 34"><circle cx="17" cy="17" r="13" fill="none" stroke="#fff" stroke-width="3"/></svg></div>
    <h3>Environmental</h3><p>Desulfurization and denitrification using our proprietary flue gas</p></div>
  <div class="feature" style="left:272px;top:88px">
    <div class="feature-icon"><svg width="34" height="34" viewBox="0 0 34 34"><path d="M4 28 L13 16 L20 22 L30 8" fill="none" stroke="#fff" stroke-width="3"/></svg></div>
    <h3>Pollution control</h3><p>Desulfurization and denitrification using our proprietary flue gas</p></div>
  <div class="feature" style="left:500px;top:50px">
    <div class="feature-icon"><svg width="34" height="34" viewBox="0 0 34 34"><path d="M6 18 L14 26 L28 8" fill="none" stroke="#fff" stroke-width="3"/></svg></div>
    <h3>Solutions employing</h3><p>Desulfurization and denitrification using our proprietary flue gas</p></div>
  <div class="feature" style="left:728px;top:20px">
    <div class="feature-icon"><svg width="34" height="34" viewBox="0 0 34 34"><path d="M17 4 Q30 16 17 30 Q4 16 17 4 Z" fill="#fff"/></svg></div>
    <h3>Nature's steal</h3><p>Desulfurization and denitrification using our proprietary flue gas</p></div>
  <div class="feature" style="left:955px;top:40px">
    <div class="feature-icon"><svg width="34" height="34" viewBox="0 0 34 34"><path d="M12 4 H22 M14 4 V14 L6 28 H28 L20 14 V4" fill="none" stroke="#fff" stroke-width="3"/></svg></div>
    <h3>Reactive Free</h3><p>Desulfurization and denitrification using our proprietary flue gas</p></div>
</section>

<section class="solutions">
  <h2 class="section-title">OUR SOLUTIONS</h2>
  <p class="solutions-intro">Desulfurization and denitrification using our proprietary flue gas advanced oxidation process. Sulfur and nitrogen are oxidized and absorbed into an environmentally friendly solid residue for safe removal.</p>
  <div class="solution-grid">
    <article class="solution-card">
      <div class="solution-photo" role="img" aria-label="Refinery pipework and tanks" style="background:linear-gradient(160deg,#9bb1c4,#4b5e70)"></div>
      <h3>Fuel HG Desulfurization</h3>
      <p>Our proprietary low-temperature process uses advanced oxidation to remove sulfur safely from fuel.</p>
      <span class="more">Read More &gt;&gt;</span></article>
    <article class="solution-card">
      <div class="solution-photo" role="img" aria-label="Industrial plant with chemical storage" style="background:linear-gradient(160deg,#c9b48a,#6c6a5e)"></div>
      <h3>Volatile Organic Compounds (VOC)</h3>
      <p>Our proprietary low-temperature process uses advanced oxidation to break down organic vapours.</p>
      <span class="more">Read More &gt;&gt;</span></article>
    <article class="solution-card">
      <div class="solution-photo" role="img" aria-label="Smokestacks releasing flue gas against the sky" style="background:linear-gradient(180deg,#8fb6d8,#3f4f60)"></div>
      <h3>Flue Gas Scrubbing</h3>
      <p>Our proprietary low-temperature process uses advanced oxidation to scrub sulfur and nitrogen oxides.</p>
      <span class="more">Read More &gt;&gt;</span></article>
    <article class="solution-card">
      <div class="solution-photo" role="img" aria-label="Wastewater flowing from an outlet pipe" style="background:linear-gradient(170deg,#7a8a6a,#3c4a3a)"></div>
      <h3>Wastewater Treatment</h3>
      <p>Our proprietary low-temperature process uses advanced oxidation to clean industrial wastewater streams.</p>
      <span class="more">Read More &gt;&gt;</span></article>
  </div>
  <svg class="wave-bottom" width="1200" height="70" viewBox="0 0 1200 70" preserveAspectRatio="none">
    <path d="M0 40 Q300 0 600 30 Q900 60 1200 20 V70 H0 Z" fill="#fff"/>
  </svg>
</section>

<section class="partners">
  <div class="partners-head"><span></span><h2>OUR PARTNERS</h2><span></span></div>
  <div class="partner-row">
    <div class="partner"><div class="partner-badge"><span class="brand-name">Velqua</span></div><p>Our sales partner<br>in China</p></div>
    <div class="partner"><div class="partner-badge"><span class="partner-shape" style="background:#e59a2a"></span></div><p>Our construction partner<br>in China</p></div>
    <div class="partner"><div class="partner-badge"><span class="partner-shape" style="background:#3b5fa8"></span></div><p>Our research partner<br>in China</p></div>
    <div class="partner"><div class="partner-badge"><span class="partner-shape" style="background:#b0333b"></span></div><p>Our technology partner<br>in China</p></div>
  </div>
</section>

<footer class="site-footer">
  <div class="footer-col" style="left:56px;width:300px">
    <h4>WELCOME</h4>
    <p>We welcome inquiries regarding the licensing, development, and purchase of our products, services, and technologies.</p>
    <a class="btn">About Us</a>
  </div>
  <div class="footer-col" style="left:420px;width:260px">
    <h4>CONTACTS</h4>
    <div class="contact-line"><svg width="10" height="12" viewBox="0 0 10 12"><path d="M5 12 Q0 6 0 4.5 A5 5 0 0 1 10 4.5 Q10 6 5 12 Z" fill="#1b8fd4"/></svg>18 Lumen Park Way, Harbor City</div>
    <div class="contact-line"><svg width="10" height="12" viewBox="0 0 10 12"><path d="M1 1 H4 L5 4 L3 5 Q4 8 6 9 L7 7 L10 8 V11 Q3 11 1 1 Z" fill="#1b8fd4"/></svg>+1 (555) 014-2208</div>
    <div class="contact-line"><svg width="12" height="10" viewBox="0 0 12 10"><rect x="0.5" y="0.5" width="11" height="9" fill="none" stroke="#1b8fd4"/><path d="M0.5 0.5 L6 5 L11.5 0.5" fill="none" stroke="#1b8fd4"/></svg>hello@velquaresearch.example</div>
  </div>
  <div class="footer-col" style="left:730px">
    <h4>FOLLOW US</h4>
    <div class="social">
      <span style="background:#3b5a9a"></span><span style="background:#2fa5dc"></span><span style="background:#d04a3c"></span><span style="background:#c23a2f"></span>
      <span style="background:#1d7ab3"></span><span style="background:#e07b25"></span><span style="background:#5b8c3a"></span><span style="background:#8a5ba8"></span>
    </div>
  </div>
  <div class="footer-brand"><span class="brand-dot"></span><span class="brand-name">Velqua</span></div>
</footer>
<div class="footer-bottom"><span>© 2016 www.velquaresearch.example</span><span>Top</span></div>

</body>
</html>
```